Commercial Rooftop Solar business needs a website

We need a website with fantastic appeal for a new company based in Melbourne called Tallow Ridge Energy. We design and install solar energy systems for commercial applications across Australia. Our market is to focus on small to medium businesses looking for solar solutions, but we will also provide our service for residential customers. We would like a beautiful 'front page' feel to our home page, using photographs of solar PV systems and/or natural imagery. Our logo uses the colours orange and black, which could easily be echoed in photographic imagery of sunset and sunrise, for example. The design should communicate quiet confidence and professionalism to a corporate marketplace.

NEW POINTS FOR BRIEF: This design also needs to be flexible to allow for additional future content, including a Support page with sub pages, FAQ's, and a Blog.

As part of this design project, we will require the coding for the website to be completed by the designer.

We have seen some websites, which we like the look and feel of: these are listed below.

brightvanepower.com.au:

• Beautiful images underlaying brief text selling points.
• Simple ‘front cover’ style home page with elegant drop-down menu, stylish simple font style.
• Home page invites exploration through the menu links, rather than trying to provide all the information up front.
• Company logo and name in the top left hand corner, contact details accessible at top right hand, seems consistent in most sites.

kelpworks.com.au

rumbofield.com:
• Same element as the others is the front-page style home page with beautiful images underlying text.

We have a webpage that we started uploading content to. You can use some of the content there in your designs: www.tallowridgeenergy.com.au

Technical Specifications:
PAGES:

Home

About Us

Solutions - Commercial
- Residential

Products - Solar Panels - Vorla Heron, Vorla TELD, Vorla QB
- Solar Inverters - Kestamo, BrilQuill
- Monitoring systems - Dunmere Metrics
- Batteries - RW

- Datasheets have been provided for reference but if it's too much work, you can use generic text and we will provide content later.

Contact Us

FUTURE PAGES (Please consider in structure, where links could be placed):

Support

FAQ's

Blog.

We could provide some content for the Support page soon, but the Blog and FAQ's are future pages which we don't want highlighted in the design as we don't yet have content.

Phone: 1800 7 BIRCH
Email: sales@tallowridgeenergy.com.au

Currently, I do not have images and text available. Please
use placeholders in the meantime. The final text and images will be uploaded for the winner once a winning design has been selected.

Target Market(s)

Primary focus is on small to medium sized business owners. Those owners will have a house which may be suitable for solar so we want to cater to residential deeper in the website.

Industry/Entity Type

Solar Energy

Coding

Coded - Design and coding required

Number of Pages Required

5+ page

Colors
f78f20
0255a3

Requirements
Must have
• Logo as per attachments.
Nice to have
• Logo can have alternate colours Eg. White on Orange or Black etc. provided colour correct logo is shown somewhere eg. footer or contact page.
• In the active site, I'd like to have:
• Very slowly zooming images - barely perceptible.
• Title text that rolls into place
• Subtle movements
• See https://plumtally.com.au/ for example

```html
<!DOCTYPE html>
<html lang="en">
<head>
<meta charset="utf-8">
<title>Tallow Ridge Energy</title>
<link href="https://fonts.googleapis.com/css2?family=Open+Sans:wght@400;600;700&family=Raleway:wght@500;600;700;800&display=swap" rel="stylesheet">
<style>
:root{
  --orange:#ef5b25;
  --ink:#222;
  --text:#555;
  --muted:#777;
  --line:#ddd;
  --soft:#f5f5f5;
  --footer:#1b1b1b;
  --white:#fff;
}
*{margin:0;padding:0;box-sizing:border-box}
html,body{width:1200px;height:3191px;overflow:hidden;background:var(--white)}
body{position:relative;font-family:"Open Sans",Arial,sans-serif;color:var(--text)}
.abs{position:absolute}

/* hero */
.hero{position:absolute;left:0;top:0;width:1200px;height:571px;overflow:hidden}
.hero-photo{position:absolute;inset:0;background:
  radial-gradient(ellipse 320px 220px at 600px 420px,rgba(255,170,60,.95),rgba(230,110,30,.55) 45%,transparent 75%),
  linear-gradient(180deg,#3d3a44 0%,#5a4c4c 40%,#8b5a30 70%,#2a2320 100%)}
.hero-shade{position:absolute;inset:0;background:rgba(0,0,0,.18)}
.brand{position:absolute;left:76px;top:38px;display:flex;align-items:center;gap:12px;color:var(--white);font-family:"Raleway",sans-serif;font-weight:700;font-size:23px;letter-spacing:1px}
.brand-dot{width:30px;height:30px;border-radius:50%;background:var(--white)}
.topphone{position:absolute;right:75px;top:12px;display:flex;align-items:center;gap:12px;color:var(--white);font-size:15px;font-weight:600}
.topphone .ic{width:28px;height:28px;border-radius:50%;background:var(--orange);display:flex;align-items:center;justify-content:center}
.nav{position:absolute;right:75px;top:60px;display:flex;gap:17px;font-family:"Raleway",sans-serif;font-weight:700;font-size:15px;color:var(--white);align-items:center}
.nav .on{color:var(--orange)}
.caret{display:inline-block;border:4px solid transparent;border-top-color:var(--white);margin-left:5px;vertical-align:middle;margin-top:4px}
.hero h1{position:absolute;left:0;width:1200px;top:170px;text-align:center;color:var(--white);font-weight:700;font-size:58px;letter-spacing:.5px}
.hero .lead{position:absolute;left:240px;width:720px;top:258px;text-align:center;color:var(--white);font-size:24px;line-height:36px}
.hero .btn{position:absolute;left:504px;top:362px;width:192px;height:46px;border:2px solid var(--white);border-radius:4px;color:var(--white);font-family:"Raleway",sans-serif;font-weight:700;font-size:15px;display:flex;align-items:center;justify-content:center}
.arrow-side{position:absolute;top:275px}
.scroll{position:absolute;left:586px;top:482px;width:28px;height:44px;border:2px solid var(--white);border-radius:14px}

/* section titles */
.sec-title{position:absolute;left:0;width:1200px;text-align:center;font-family:"Raleway",sans-serif;font-weight:800;font-size:34px;color:var(--ink)}
.rule{position:absolute;left:560px;width:80px;height:3px;background:var(--orange)}

/* welcome */
.intro{position:absolute;left:220px;width:760px;top:748px;text-align:center;font-size:13px;line-height:24px;color:var(--muted)}
.feature{position:absolute;width:320px;display:flex;gap:20px}
.feature .circ{flex:none;width:80px;height:80px;border-radius:50%;border:2px solid var(--line);display:flex;align-items:center;justify-content:center}
.feature h3{font-family:"Raleway",sans-serif;font-weight:600;font-size:19px;color:var(--ink);margin-top:6px;margin-bottom:10px}
.feature p{font-size:12px;line-height:24px;color:var(--muted);width:200px}

/* how it works */
.how{position:absolute;left:0;top:1130px;width:1200px;height:570px}
.how-title{position:absolute;left:0;top:1273px;width:1200px;text-align:center;font-family:"Raleway",sans-serif;font-weight:800;font-size:34px;color:var(--white)}
.step{position:absolute;width:220px;text-align:center;color:var(--white);font-size:13px;line-height:21px}
.pin{position:absolute}

/* solutions */
.solutions{position:absolute;left:0;top:1690px;width:1200px;height:778px;background:var(--soft)}
.card-photo{position:absolute;width:476px;height:262px;border:4px solid var(--white);box-shadow:0 0 0 1px #e6e6e6}
.card h3{position:absolute;font-family:"Raleway",sans-serif;font-weight:700;font-size:25px;color:var(--ink)}
.card p{position:absolute;width:476px;font-size:13px;line-height:26px;color:var(--muted)}
.more{position:absolute;width:122px;height:38px;border:2px solid #ccc;border-radius:4px;background:var(--white);color:var(--orange);font-weight:700;font-size:12px;display:flex;align-items:center;justify-content:center}

/* products */
.tile{position:absolute;top:2643px;width:176px;height:84px;border:3px solid #e2e2e2;display:flex;align-items:center;justify-content:center;font-family:"Raleway",sans-serif;font-weight:600;font-size:26px;color:#8a8a8a;background:var(--white)}

/* footer */
.footer{position:absolute;left:0;top:2812px;width:1200px;height:379px;background:var(--footer);border-top:5px solid var(--orange)}
.f-brand{position:absolute;left:95px;top:2930px;display:flex;align-items:center;gap:10px;color:var(--white);font-family:"Raleway",sans-serif;font-weight:700;font-size:18px;line-height:22px}
.f-brand .brand-dot{width:24px;height:24px}
.f-head{position:absolute;top:2870px;font-family:"Raleway",sans-serif;font-weight:700;font-size:17px;color:var(--white)}
.f-row{position:absolute;display:flex;align-items:center;gap:16px;color:var(--white);font-size:13px}
.f-text{position:absolute;left:622px;top:2912px;width:290px;font-size:12px;line-height:21px;color:var(--white)}
.f-input{position:absolute;left:622px;top:2966px;width:284px;height:40px;background:var(--white);color:#444;font-size:12px;padding:12px 14px}
.f-sub{position:absolute;left:622px;top:3018px;width:114px;height:40px;background:var(--orange);color:var(--white);font-weight:700;font-size:13px;display:flex;align-items:center;justify-content:center}
.f-links{position:absolute;left:985px;top:2912px;list-style:none;font-size:13px;line-height:24px;color:var(--white)}
.copy{position:absolute;left:0;top:3078px;width:1200px;text-align:center;font-size:12px;color:var(--white)}
</style>
</head>
<body>

<header class="hero">
  <div class="hero-photo" role="img" aria-label="City skyline at sunset with the sun glowing between high-rise towers over the water"></div>
  <div class="hero-shade"></div>
  <div class="brand"><span class="brand-dot"></span>TALLOW RIDGE ENERGY</div>
  <div class="topphone"><span class="ic"><svg width="14" height="14" viewBox="0 0 24 24"><path fill="#fff" d="M6.6 10.8a15 15 0 0 0 6.6 6.6l2.2-2.2c.3-.3.7-.4 1-.2 1.1.4 2.3.6 3.6.6.6 0 1 .4 1 1V20c0 .6-.4 1-1 1A17 17 0 0 1 3 4c0-.6.4-1 1-1h3.5c.6 0 1 .4 1 1 0 1.3.2 2.5.6 3.6.1.3 0 .7-.2 1z"/></svg></span>1800 7 BIRCH</div>
  <nav class="nav">
    <span class="on">HOME</span><span>ABOUT US</span><span>SOLUTIONS<i class="caret"></i></span><span>PRODUCTS</span><span>SUPPORT</span><span>FAQ'S</span><span>CONTACT US</span>
    <svg width="16" height="16" viewBox="0 0 24 24"><circle cx="10" cy="10" r="7" fill="none" stroke="#fff" stroke-width="3"/><path d="M15 15l6 6" stroke="#fff" stroke-width="3"/></svg>
  </nav>
  <h1>TALLOW RIDGE ENERGY</h1>
  <p class="lead">We design and install solar energy systems for commercial applications across Australia</p>
  <div class="btn">GET MORE INFO</div>
  <svg class="arrow-side" style="left:10px" width="14" height="22" viewBox="0 0 14 22"><path d="M12 2L3 11l9 9" fill="none" stroke="#ddd" stroke-width="2"/></svg>
  <svg class="arrow-side" style="right:10px" width="14" height="22" viewBox="0 0 14 22"><path d="M2 2l9 9-9 9" fill="none" stroke="#ddd" stroke-width="2"/></svg>
  <div class="scroll"><svg width="24" height="40" viewBox="0 0 24 40"><path d="M7 14l5 5 5-5M7 21l5 5 5-5" fill="none" stroke="#fff" stroke-width="2"/></svg></div>
</header>

<section class="welcome">
  <h2 class="sec-title" style="top:652px">WELCOME TO TALLOW RIDGE ENERGY</h2>
  <div class="rule" style="top:710px"></div>
  <p class="intro">We plan, build and look after solar systems that cut running costs for Australian businesses, with clear advice at every step and a local team that stays with you long after the panels are switched on.</p>

  <div class="feature" style="left:98px;top:850px"><div class="circ"><svg width="34" height="34" viewBox="0 0 24 24"><rect x="3" y="5" width="14" height="15" rx="2" fill="none" stroke="#ef5b25" stroke-width="2"/><path d="M9 14l9-9 2 2-9 9H9z" fill="#ef5b25"/></svg></div><div><h3>System Design</h3><p>Layouts sized to your roof and daily load.</p></div></div>
  <div class="feature" style="left:454px;top:850px"><div class="circ"><svg width="36" height="36" viewBox="0 0 24 24"><circle cx="9" cy="10" r="4" fill="none" stroke="#ef5b25" stroke-width="3" stroke-dasharray="2 1.2"/><circle cx="17" cy="16" r="3" fill="none" stroke="#ef5b25" stroke-width="2.5" stroke-dasharray="1.6 1"/></svg></div><div><h3>Operational Management</h3><p>Ongoing checks that keep output steady year round.</p></div></div>
  <div class="feature" style="left:815px;top:850px"><div class="circ"><svg width="34" height="34" viewBox="0 0 24 24"><path d="M14 3a5 5 0 0 0-4.6 6.8L3 16.2 5.8 19l6.4-6.4A5 5 0 0 0 19 8l-3 3-3-3 3-3a5 5 0 0 0-2-2z" fill="#ef5b25"/></svg></div><div><h3>Installation</h3><p>Accredited crews fitting panels safely and on time.</p></div></div>

  <div class="feature" style="left:98px;top:988px"><div class="circ"><svg width="36" height="36" viewBox="0 0 24 24"><circle cx="12" cy="12" r="5" fill="#ef5b25"/><g stroke="#ef5b25" stroke-width="2"><path d="M12 1v4M12 19v4M1 12h4M19 12h4M4 4l3 3M17 17l3 3M20 4l-3 3M7 17l-3 3"/></g></svg></div><div><h3>Solar Irrigation</h3><p>Solar pumping for farms and remote sites.</p></div></div>
  <div class="feature" style="left:454px;top:988px"><div class="circ"><svg width="38" height="38" viewBox="0 0 24 24"><rect x="2" y="7" width="18" height="10" rx="1" fill="none" stroke="#ef5b25" stroke-width="2"/><rect x="4" y="9" width="14" height="6" fill="#ef5b25"/><rect x="20" y="10" width="2" height="4" fill="#ef5b25"/></svg></div><div><h3>Energy Storage</h3><p>Battery storage that holds power for evening use.</p></div></div>
  <div class="feature" style="left:815px;top:988px"><div class="circ"><svg width="34" height="34" viewBox="0 0 24 24"><path d="M12 2a7 7 0 0 0-4 12.7V17h8v-2.3A7 7 0 0 0 12 2z" fill="none" stroke="#ef5b25" stroke-width="2"/><path d="M9 20h6M10 23h4" stroke="#ef5b25" stroke-width="2"/></svg></div><div><h3>Feasibility Study</h3><p>Site review of savings, shading and payback.</p></div></div>
</section>

<section class="how">
  <svg width="1200" height="570" viewBox="0 0 1200 570" style="position:absolute;left:0;top:0" role="img" aria-label="Field of solar panels under a dusky evening sky">
    <defs>
      <linearGradient id="howfill" x1="0" y1="0" x2="0" y2="1">
        <stop offset="0" stop-color="#4a4f5a"/><stop offset=".3" stop-color="#2f3646"/><stop offset="1" stop-color="#1c2438"/>
      </linearGradient>
    </defs>
    <polygon points="0,8 1200,115 1200,480 0,560" fill="url(#howfill)"/>
  </svg>
  <h2 class="how-title" style="top:143px">HOW IT WORKS</h2>
  <div class="rule" style="top:190px"></div>
</section>
<svg class="pin" style="left:144px;top:1365px" width="92" height="100" viewBox="0 0 92 100"><path d="M46 2a44 44 0 0 1 8 87l-8 10-8-10A44 44 0 0 1 46 2z" fill="none" stroke="#fff" stroke-width="2"/><circle cx="46" cy="38" r="9" fill="#fff"/><path d="M28 64a18 14 0 0 1 36 0z" fill="#fff"/></svg>
<svg class="pin" style="left:422px;top:1365px" width="92" height="100" viewBox="0 0 92 100"><path d="M46 2a44 44 0 0 1 8 87l-8 10-8-10A44 44 0 0 1 46 2z" fill="none" stroke="#fff" stroke-width="2"/><circle cx="46" cy="46" r="18" fill="none" stroke="#fff" stroke-width="2"/><circle cx="46" cy="46" r="8" fill="none" stroke="#fff" stroke-width="2"/></svg>
<svg class="pin" style="left:692px;top:1365px" width="92" height="100" viewBox="0 0 92 100"><path d="M46 2a44 44 0 0 1 8 87l-8 10-8-10A44 44 0 0 1 46 2z" fill="none" stroke="#fff" stroke-width="2"/><rect x="26" y="34" width="40" height="22" fill="#fff"/><path d="M36 34v22M46 34v22M56 34v22M26 45h40M46 56v8M38 64h16" stroke="#2f3646" stroke-width="1.5"/><path d="M46 56v8M38 64h16" stroke="#fff" stroke-width="2"/></svg>
<svg class="pin" style="left:968px;top:1365px" width="92" height="100" viewBox="0 0 92 100"><path d="M46 2a44 44 0 0 1 8 87l-8 10-8-10A44 44 0 0 1 46 2z" fill="none" stroke="#fff" stroke-width="2"/><rect x="28" y="34" width="36" height="24" rx="2" fill="#fff"/><circle cx="46" cy="46" r="7" fill="#2f3646"/></svg>
<svg class="abs" style="left:290px;top:1402px" width="80" height="20" viewBox="0 0 80 20"><path d="M2 14q36-14 70-2" fill="none" stroke="#fff" stroke-width="2" stroke-dasharray="5 4"/><path d="M68 6l7 6-8 4" fill="none" stroke="#fff" stroke-width="2"/></svg>
<svg class="abs" style="left:573px;top:1420px" width="80" height="20" viewBox="0 0 80 20"><path d="M2 14q36-14 70-2" fill="none" stroke="#fff" stroke-width="2" stroke-dasharray="5 4"/><path d="M68 6l7 6-8 4" fill="none" stroke="#fff" stroke-width="2"/></svg>
<svg class="abs" style="left:835px;top:1402px" width="80" height="20" viewBox="0 0 80 20"><path d="M2 14q36-14 70-2" fill="none" stroke="#fff" stroke-width="2" stroke-dasharray="5 4"/><path d="M68 6l7 6-8 4" fill="none" stroke="#fff" stroke-width="2"/></svg>
<p class="step" style="left:80px;top:1488px">Tallow Ridge Energy checks that every person gets a solar system that pays for itself in energy savings from day one</p>
<p class="step" style="left:358px;top:1488px">Tallow Ridge Energy organises for the solar system to be installed</p>
<p class="step" style="left:628px;top:1488px">Tallow Ridge Energy supports pensioners to understand and get the most out of solar</p>
<p class="step" style="left:904px;top:1488px">Pensioners gradually pay for cost through their usual rates payments at 0% interest</p>

<section class="solutions">
  <h2 class="sec-title" style="top:54px">OUR SOLUTIONS</h2>
  <div class="rule" style="top:108px"></div>
  <div class="card">
    <div class="card-photo" style="left:98px;top:172px;background:linear-gradient(180deg,#f0a030 0%,#e86a20 40%,#b5442a 60%,#7a3030 100%)" role="img" aria-label="Rows of solar panels in a field at sunset"></div>
    <h3 style="left:98px;top:465px">COMMERCIAL</h3>
    <p style="left:98px;top:525px">Solar for offices, warehouses and retail sites, designed around your trading hours so more of each panel's output is used on site and your power bills fall from the first month of operation.</p>
    <div class="more" style="left:98px;top:660px">READ MORE &gt;&gt;</div>
  </div>
  <div class="card">
    <div class="card-photo" style="left:626px;top:172px;background:linear-gradient(160deg,#c9b27a 0%,#9aa3a8 40%,#6f7a86 70%,#3e4248 100%)" role="img" aria-label="Close view of solar panels mounted on a house roof with trees behind"></div>
    <h3 style="left:626px;top:465px">RESIDENTIAL</h3>
    <p style="left:626px;top:525px">Home systems for owners who want the same care they get at work, with quality panels, tidy installs and simple monitoring so you can see what your roof earns each and every day.</p>
    <div class="more" style="left:626px;top:660px">READ MORE &gt;&gt;</div>
  </div>
</section>

<section class="products">
  <h2 class="sec-title" style="top:2533px">OUR PRODUCTS</h2>
  <div class="rule" style="top:2587px"></div>
  <div class="tile" style="left:98px">Brisko</div>
  <div class="tile" style="left:305px;font-size:20px;letter-spacing:3px">ENVOYRA</div>
  <div class="tile" style="left:512px">Talvane</div>
  <div class="tile" style="left:719px;font-size:22px">Loftwise</div>
  <div class="tile" style="left:926px;font-size:22px">Gainstead</div>
</section>

<footer>
  <div class="footer"></div>
  <div class="f-brand"><span class="brand-dot"></span>TALLOW RIDGE<br>ENERGY</div>
  <h4 class="f-head" style="left:310px">CONTACT US</h4>
  <div class="f-row" style="left:310px;top:2924px"><svg width="16" height="16" viewBox="0 0 24 24"><path fill="none" stroke="#fff" stroke-width="2" d="M6.6 10.8a15 15 0 0 0 6.6 6.6l2.2-2.2c.3-.3.7-.4 1-.2 1.1.4 2.3.6 3.6.6.6 0 1 .4 1 1V20c0 .6-.4 1-1 1A17 17 0 0 1 3 4c0-.6.4-1 1-1h3.5c.6 0 1 .4 1 1 0 1.3.2 2.5.6 3.6.1.3 0 .7-.2 1z"/></svg>1800 7 BIRCH</div>
  <div class="f-row" style="left:310px;top:2972px"><svg width="16" height="12" viewBox="0 0 16 12"><rect x="1" y="1" width="14" height="10" fill="none" stroke="#fff" stroke-width="1.5"/><path d="M1 1l7 6 7-6" fill="none" stroke="#fff" stroke-width="1.5"/></svg>sales@tallowridgeenergy.com.au</div>
  <h4 class="f-head" style="left:622px">SIGN UP TO RECEIVE EMAIL</h4>
  <p class="f-text">Get project news, rebate updates and seasonal tips sent straight to your inbox.</p>
  <div class="f-input">Enter Email</div>
  <div class="f-sub">SUBSCRIBE</div>
  <h4 class="f-head" style="left:985px">QUICK LINKS</h4>
  <ul class="f-links"><li>Home</li><li>About Us</li><li>Solutions</li><li>Projects</li><li>Blog</li><li>Contact Us</li></ul>
  <p class="copy">Copyright © Tallow Ridge Energy 2017. All rights reserved.</p>
</footer>

</body>
</html>
```